Sparrowlane Calculator Redesign

Sparrowlane is jewelry featuring the picture of the moon from the date of your choice such as your birthday or anniversarry. People come to our moon phase calculator page (you are designing) to see what the moon looked like on a specific date. I have attached a draft for inspiration. We would like the mockup in both mobile and desktop please.

Give us your best designs to have people engaged with our moon phase calculator page and want to continue navigating and shopping the site
Updates

The Moon must be black so it seems realistic.

Target Market(s)

Woman and men, 25-45

Industry/Entity Type

Jewelry

Colors
6B429C
8869AF
B7A5CE
E3DAEB
F3F0F8

Requirements
Must have
• The moon phase date selection and content speaking about their moonphase
Should not have
• Pink

```html
<!DOCTYPE html>
<html lang="en">
<head>
<meta charset="utf-8">
<title>Sparrowlane – Moon Phase Calculator</title>
<link rel="stylesheet" href="https://fonts.googleapis.com/css2?family=Catamaran:wght@500;600;700&family=Lato:wght@400;700&display=swap">
<style>
:root{
  --purple:#5b2d91;
  --purple-mid:#6B429C;
  --lilac:#8869AF;
  --lilac-soft:#B7A5CE;
  --lilac-pale:#E3DAEB;
  --lilac-mist:#F3F0F8;
  --night:#24124a;
  --ink:#1b1b1b;
  --text:#333;
  --beige:#ece5de;
  --white:#fff;
  --star:#f29a1f;
}
*{box-sizing:border-box;margin:0;padding:0}
html,body{width:1200px;height:3601px;overflow:hidden}
body{position:relative;font-family:"Lato",sans-serif;color:var(--text);background:var(--white)}
.abs{position:absolute}
h1,h2,h3{font-family:"Catamaran",sans-serif;color:var(--ink)}

/* top bar */
.promo-bar{left:0;top:0;width:1200px;height:37px;background:var(--purple);color:var(--white);font-size:14px;text-align:center;line-height:37px}

/* header */
.search{left:112px;top:60px;width:248px;height:42px;border:1px solid #555;font-size:14px;color:#555;padding:0 16px;line-height:40px}
.search svg{position:absolute;right:16px;top:12px}
.brand{left:400px;top:74px;width:400px;text-align:center;font-size:27px;letter-spacing:3px;color:var(--purple-mid);font-weight:400}
.brand .dot{display:inline-block;width:12px;height:12px;border-radius:50%;background:var(--purple-mid);margin-right:10px;vertical-align:middle}
.login{left:821px;top:60px;width:99px;height:37px;border-radius:19px;background:var(--purple);color:var(--white);font-family:"Catamaran",sans-serif;font-weight:600;font-size:15px;line-height:37px;text-align:right;padding-right:21px}
.login svg{position:absolute;left:17px;top:11px}
.cart{left:950px;top:68px;font-family:"Catamaran",sans-serif;font-weight:600;font-size:15px;color:var(--ink)}
.cart svg{vertical-align:-3px;margin-right:8px}
.main-nav{left:0;top:128px;width:1200px;height:32px;border-bottom:1px solid #ddd}
.main-nav a{position:absolute;top:0;font-size:15px;color:var(--ink);text-decoration:none}
.main-nav a.active{color:var(--purple-mid)}
.main-nav a.active::after{content:"";position:absolute;left:0;right:0;top:28px;height:2px;background:var(--purple-mid)}

/* hero */
.hero{left:0;top:160px;width:1200px;height:573px;background:radial-gradient(ellipse at 60% 40%,#3b2370 0%,var(--night) 70%)}
.hero-moon{left:147px;top:266px;width:380px;height:380px;border-radius:50%;background:radial-gradient(circle at 40% 38%,#3d3d42 0%,#1c1c20 55%,#07070a 100%);box-shadow:0 0 30px rgba(183,165,206,.35)}
.hero-title{left:621px;top:322px;width:520px;color:var(--white);font-size:43px;line-height:50px;font-weight:700}
.hero-text{left:621px;top:440px;width:460px;color:var(--white);font-size:15px;line-height:26px}
.btn-light{left:622px;top:511px;width:228px;height:45px;border-radius:23px;background:var(--white);color:var(--purple);font-family:"Catamaran",sans-serif;font-weight:700;font-size:15px;text-align:center;line-height:45px}

/* feature tiles */
.tile{top:771px;width:320px;height:327px;overflow:hidden}
.tile .photo{position:absolute;inset:0}
.tile .label{position:absolute;left:0;right:0;top:145px;text-align:center;font-family:"Catamaran",sans-serif;font-weight:700;font-size:25px;color:var(--white)}
.tile-feature .photo{background:linear-gradient(160deg,#6a4f8a,#4d3470)}
.tile-feature .frame{position:absolute;left:10px;top:10px;right:10px;bottom:10px;border:3px solid var(--lilac-pale);background:rgba(107,66,156,.82);text-align:center;color:var(--white);padding:58px 24px 0}
.tile-feature h3{color:var(--white);font-size:26px;font-weight:700;margin-bottom:10px}
.tile-feature p{font-size:14.5px;line-height:26px;color:#eee}
.tile-feature .more{margin-top:12px;font-size:15px}

/* pair section */
.pair-title{left:112px;top:1184px;font-size:34px;font-weight:700}
.pair-text{left:112px;width:520px;font-size:14.5px;line-height:26px;color:var(--text)}
.pill{height:46px;border-radius:23px;background:var(--purple);color:var(--white);font-family:"Catamaran",sans-serif;font-weight:700;font-size:15px;line-height:46px;overflow:hidden}
.pill::before{content:"";position:absolute;left:10px;top:7px;width:32px;height:32px;border-radius:50%;background:var(--lilac-soft);box-shadow:inset -9px 0 0 var(--purple-mid)}
.pill span{position:relative}
.pair-ring{left:673px;top:1165px;width:414px;height:410px;border-radius:50%;background:var(--purple)}
.pair-photo{left:710px;top:1180px;width:380px;height:380px;border-radius:50%;background:radial-gradient(circle at 45% 45%,#e9c7b5,#d4a996 65%,#c5988a)}

/* moments band */
.moments{left:0;top:1622px;width:1200px;height:339px;background:linear-gradient(180deg,#2e2c30,#1f1f23 60%,#302b2a)}
.moments-title{left:0;top:1676px;width:1200px;text-align:center;color:var(--white);font-size:34px;font-weight:700}
.moments-text{left:160px;top:1735px;width:880px;text-align:center;color:#eee;font-size:15px;line-height:26px}

/* products */
.loved-title{left:0;top:2026px;width:1200px;text-align:center;font-size:34px;font-weight:700}
.product{top:2131px;width:233px;height:340px;background:var(--beige);text-align:center}
.product.raised{background:var(--white);box-shadow:0 2px 10px rgba(0,0,0,.12)}
.product .photo{position:absolute;left:0;top:0;width:100%;height:190px;background:linear-gradient(180deg,#ede6df,#e3dbd3)}
.product.raised .photo{background:linear-gradient(180deg,#fbfbfb,#f1f1f1)}
.product .stars{position:absolute;left:0;right:0;top:196px;color:var(--star);font-size:16px;letter-spacing:4px}
.product h3{position:absolute;left:0;right:0;top:232px;font-size:20px;line-height:30px;font-weight:600}
.product .price{position:absolute;left:0;right:0;top:302px;color:var(--purple-mid);font-size:16px}
.product .shop{position:absolute;left:46px;top:85px;width:138px;height:48px;border-radius:24px;background:var(--purple);color:var(--white);font-family:"Catamaran",sans-serif;font-weight:600;font-size:17px;line-height:48px}

/* calculator */
.calc-title{left:0;top:2538px;width:1200px;text-align:center;font-size:34px;font-weight:700}
.calc-photo{left:162px;top:2612px;width:411px;height:458px;background:linear-gradient(150deg,#6b5a4c,#a8907a 45%,#5d4c3f)}
.calc-name{left:625px;top:2620px;font-size:24px;font-weight:600}
.calc-amount{left:625px;top:2660px;font-family:"Catamaran",sans-serif;font-size:23px;font-weight:700;color:var(--ink)}
.calc-desc{left:625px;top:2706px;width:420px;font-size:14px;line-height:26px}
.field{left:625px;width:361px;height:42px;background:#f2f2f2;border-radius:4px;font-size:14px;color:#333;padding-left:22px;line-height:42px}
.engrave{left:645px;top:2826px;font-size:15px;font-weight:700;color:var(--ink)}
.note{left:630px;top:2926px;width:250px;font-size:11.5px;line-height:20px}
.next{left:891px;top:2923px;width:89px;height:35px;background:var(--purple);color:var(--white);font-weight:700;font-size:14px;text-align:center;line-height:35px;border-radius:3px}
.radio{left:675px;top:2972px;font-size:11.5px}
.radio::before{content:"";position:absolute;left:-16px;top:3px;width:9px;height:9px;border:1px solid #999;border-radius:50%}
.rule{left:625px;top:2991px;width:361px;height:1px;background:#ddd}
.add{left:625px;top:3015px;width:353px;height:41px;background:var(--purple);color:var(--white);font-size:12px;font-weight:700;text-align:center;line-height:41px}

/* footer */
.footer{left:0;top:3139px;width:1200px;height:462px;background:#000}
.footer-mark{left:556px;top:3190px;width:88px;height:88px;border-radius:50%;background:var(--white)}
.footer-brand{left:0;top:3292px;width:1200px;text-align:center;color:var(--white);font-size:36px;letter-spacing:2px;font-weight:400}
.footer-nav a{position:absolute;top:3372px;color:var(--white);font-size:15px;text-decoration:none}
.social{top:3423px;width:40px;height:40px;border-radius:50%;border:1.5px solid var(--white)}
.social.first{background:var(--purple);border-color:var(--purple)}
.copyright{left:0;top:3536px;width:1200px;text-align:center;color:var(--white);font-size:14.5px}
</style>
</head>
<body>

<div class="abs promo-bar">Free Returns with 30 Days | Free US shipping $50 | Safe and Secure Checkout</div>

<header>
  <div class="abs search">Search
    <svg width="16" height="16" viewBox="0 0 16 16"><circle cx="6.5" cy="6.5" r="5" fill="none" stroke="#333" stroke-width="2"/><line x1="10.5" y1="10.5" x2="15" y2="15" stroke="#333" stroke-width="2.2"/></svg>
  </div>
  <div class="abs brand"><span class="dot"></span>SPARROWLANE</div>
  <div class="abs login">
    <svg width="14" height="15" viewBox="0 0 14 15"><circle cx="7" cy="4" r="3.6" fill="#fff"/><path d="M0 15c0-4 3-6 7-6s7 2 7 6z" fill="#fff"/></svg>Login
  </div>
  <div class="abs cart">
    <svg width="18" height="15" viewBox="0 0 18 15"><path d="M1 5h16l-2 9H3z" fill="none" stroke="#222" stroke-width="1.8"/><path d="M5 5l3-4M13 5l-3-4" stroke="#222" stroke-width="1.6"/><path d="M6 8v3M9 8v3M12 8v3" stroke="#222" stroke-width="1.4"/></svg>Cart
  </div>
  <nav class="abs main-nav">
    <a class="active" style="left:371px">HOME</a>
    <a style="left:455px">SHOP</a>
    <a style="left:538px">GIFTS</a>
    <a style="left:629px">SALE</a>
    <a style="left:709px">OUR STORY</a>
  </nav>
</header>

<section>
  <div class="abs hero" role="img" aria-label="Starry night sky background"></div>
  <div class="abs hero-moon" role="img" aria-label="Photograph of the moon shown in black"></div>
  <h1 class="abs hero-title">Ready to Discover Your Moon Phase?</h1>
  <p class="abs hero-text">Using the moon phase calculator below, discover your unique moon phase from a date close to your heart!</p>
  <div class="abs btn-light">Find My Moon Phase</div>
</section>

<section>
  <div class="abs tile" style="left:112px">
    <div class="photo" role="img" aria-label="Gold moon phase necklace and ring on white fabric" style="background:linear-gradient(135deg,#e9e2d8,#d8cec2 50%,#c6b9aa)"></div>
    <div class="label">Your Birth Moon</div>
  </div>
  <div class="abs tile tile-feature" style="left:440px">
    <div class="photo" role="img" aria-label="Moon phase jewelry on fabric"></div>
    <div class="frame">
      <h3>Your Anniversary</h3>
      <p>Lorem ipsum dolor sit amet, consectetur adipiscing elit, sed do eiusmod tempor incididunt ut labore et dolore magna aliqua.</p>
      <div class="more">Learn More &nbsp;»</div>
    </div>
  </div>
  <div class="abs tile" style="left:768px">
    <div class="photo" role="img" aria-label="Woman wearing a moon phase pendant" style="background:linear-gradient(135deg,#9c7a66,#c8a590 50%,#b19380)"></div>
    <div class="label">Your Moon Sign</div>
  </div>
</section>

<section>
  <h2 class="abs pair-title">The Perfect Pair: His &amp; Hers</h2>
  <p class="abs pair-text" style="top:1247px">Love burns bright at Sparrowlane and we are honored to help make your love story glow! Find your unique moon phases using our special moon calculator and then find a piece that speaks to you.</p>
  <p class="abs pair-text" style="top:1350px">Our new matte black men's moon phase bracelet is the perfect lunar twin to the Crescent Link Bracelet for her!</p>
  <p class="abs pair-text" style="top:1428px">Choose your twin birth moons, the Moment you both said 'I do', or the moon you began your journey under!</p>
  <div class="abs pill" style="left:112px;top:1501px;width:136px;padding-left:29px"><span>Learn More</span></div>
  <div class="abs pair-ring"></div>
  <div class="abs pair-photo" role="img" aria-label="Woman holding a silver hand pendant with a purple stone"></div>
</section>

<section>
  <div class="abs moments" role="img" aria-label="Dim photograph of hands holding jewelry"></div>
  <h2 class="abs moments-title">Meet The Moments</h2>
  <p class="abs moments-text">Lorem ipsum dolor sit amet, consectetur adipiscing elit, sed do eiusmod tempor incididunt ut labore et dolore magna aliqua. Quis ipsum suspendisse ultrices gravida. Risus commodo viverra maecenas accumsan lacus vel facilisis. Lorem ipsum dolor sit amet, consectetur adipiscing elit, sed do eiusmod tempor incididunt ut labore et dolore magna aliqua.</p>
  <div class="abs pill" style="left:540px;top:1839px;width:126px;text-align:center;padding-left:4px"><span>Shop Now</span></div>
</section>

<section>
  <h2 class="abs loved-title">Sparrowlane's Most Loved</h2>
  <div class="abs product" style="left:112px">
    <div class="photo" role="img" aria-label="Silver moon phase necklace"></div>
    <div class="stars">★★★★★</div>
    <h3>Starfall Necklace<br>in Silver</h3>
    <div class="price">$49</div>
  </div>
  <div class="abs product raised" style="left:359px">
    <div class="photo" role="img" aria-label="Gold necklace with turquoise stone"></div>
    <div class="shop">Shop Now</div>
    <div class="stars">★★★★★</div>
    <h3>Orbit Necklace<br>in Gold</h3>
    <div class="price">$80 $95 15% OFF!</div>
  </div>
  <div class="abs product" style="left:607px">
    <div class="photo" role="img" aria-label="White cord bracelet with moon charm"></div>
    <div class="stars">★★★★★</div>
    <h3>Bright Tide<br>Bracelet in White</h3>
    <div class="price">$56</div>
  </div>
  <div class="abs product" style="left:856px">
    <div class="photo" role="img" aria-label="Gold heart necklace with blue stone"></div>
    <div class="stars">★★★★★</div>
    <h3>Gentle Heart<br>Necklace in Gold</h3>
    <div class="price">$95</div>
  </div>
</section>

<section>
  <h2 class="abs calc-title">Keep Your Phase Close To Heart</h2>
  <div class="abs calc-photo" role="img" aria-label="Deck of cards on satin fabric with crystals"></div>
  <h3 class="abs calc-name">Quiet Glow Necklace</h3>
  <div class="abs calc-amount">$49</div>
  <p class="abs calc-desc">Lorem ipsum dolor sit amet, consectetur adipiscing elit, sed do eiusmod tempor incididunt ut labore et dolore magna aliqua.</p>
  <div class="abs field" style="top:2770px">01 / Jan / 2000
    <svg style="position:absolute;right:14px;top:13px" width="8" height="16" viewBox="0 0 8 16"><path d="M1 6l3-4 3 4M1 10l3 4 3-4" fill="none" stroke="#333" stroke-width="1.3"/></svg>
  </div>
  <div class="abs engrave">Add Engraving</div>
  <div class="abs field" style="top:2857px">Type Your Message here
    <span style="position:absolute;right:14px;top:-6px;font-size:15px;font-weight:700">×</span>
  </div>
  <p class="abs note">Lorem ipsum dolor sit amet, consectetur adipiscing elit, sed do eiusmod</p>
  <div class="abs next">Next</div>
  <div class="abs radio">Lorem ipsum dolor sit amet, consectetur</div>
  <div class="abs rule"></div>
  <div class="abs add">Add To Cart</div>
</section>

<footer>
  <div class="abs footer"></div>
  <div class="abs footer-mark"></div>
  <div class="abs footer-brand">SPARROWLANE</div>
  <nav class="footer-nav">
    <a style="left:390px">HOME</a>
    <a style="left:473px">SHOP</a>
    <a style="left:557px">GIFTS</a>
    <a style="left:648px">SALE</a>
    <a style="left:727px">OUR STORY</a>
  </nav>
  <div class="abs social first" style="left:508px" aria-label="Social link"></div>
  <div class="abs social" style="left:556px" aria-label="Social link"></div>
  <div class="abs social" style="left:604px" aria-label="Social link"></div>
  <div class="abs social" style="left:651px" aria-label="Social link"></div>
  <div class="abs copyright">©Copyrights 2022 &nbsp;Sparrowlane &nbsp; | &nbsp; All Rights Reserved</div>
</footer>

</body>
</html>
```